ro dun magazine

just need coupons of real customers made for my magazine, I have the layout or temp lets of the magazine i just need the coupons to be made and plug-in. i have examples, of the ads or coupons, I'm sure they will need to redone. and in a section of the magazine their in a church directory. with this section , i need the pic of the pastor plug in with their church information and in do have some ex-samples of that as well. with the websites of the businesses. if you need to grab an image from their site . you'll be able to do so. all of the business are in the upload section , these are small base business so a lot of the ads and logos need redone any way . so i will look at it and let you know.

P.S with the new coupons and logos I'm trying to impress these customers to stay with the magazine

Target Market(s)

small businesses

Requirements
Must have
• good graphics
Should not have
• not pixelated graphics

```html
<!DOCTYPE html>
<html lang="en">
<head>
<meta charset="utf-8">
<title>Church Directory</title>
<link href="https://fonts.googleapis.com/css2?family=Anton&family=Barlow+Condensed:wght@600;700&family=Barlow+Semi+Condensed:wght@400;600&family=Montserrat:wght@400;500;700;800;900&family=Great+Vibes&display=swap" rel="stylesheet">
<style>
:root{
  --ink:#111111;
  --red:#e3101c;
  --yellow:#fff200;
  --photo-yellow:#fffc00;
  --band:#eeeeb4;
  --maroon:#4a0606;
  --maroon-dark:#2a0202;
  --white:#ffffff;
}
*{margin:0;padding:0;box-sizing:border-box}
html,body{width:849px;height:1200px;overflow:hidden;background:var(--white)}
body{position:relative;font-family:"Barlow Semi Condensed",sans-serif;color:var(--ink)}

/* Banner */
.banner{position:absolute;left:21px;top:17px;width:811px;height:130px;overflow:hidden;
  background:linear-gradient(180deg,#8a7a8e 0%,#c98a86 35%,#ef9a72 62%,#f6b48a 80%,#b79b80 100%)}
.banner-scene{position:absolute;inset:0;background:linear-gradient(90deg,rgba(235,235,240,.55) 0%,rgba(235,235,240,.35) 14%,rgba(0,0,0,0) 22%)}
.banner-title{position:absolute;left:158px;top:26px;width:600px;text-align:center;font-family:"Anton",sans-serif;font-weight:400;font-size:80px;line-height:1;letter-spacing:1px;color:var(--red);
  transform:scaleY(1.08);transform-origin:top center;
  -webkit-text-stroke:2px #6b0000;paint-order:stroke fill;
  text-shadow:3px 3px 0 #fff,-3px -3px 0 #fff,3px -3px 0 #fff,-3px 3px 0 #fff,5px 6px 4px rgba(0,0,0,.45)}
.banner-cross{position:absolute;left:406px;top:12px}

/* Left promo */
.promo{position:absolute;left:21px;top:154px;width:260px;height:1020px;overflow:hidden;
  background:radial-gradient(ellipse at 50% 30%,#6a0b0b 0%,var(--maroon) 45%,var(--maroon-dark) 100%)}
.promo-photo{position:absolute;left:0;top:46px;width:260px;height:612px;
  background:linear-gradient(160deg,#3a0808 0%,#8d3b2e 25%,#d6a07f 45%,#b8563e 65%,#5a0d0d 100%)}
.promo-head{position:absolute;left:0;top:0;width:260px;height:46px;background:var(--yellow);display:flex;align-items:center;justify-content:center;gap:8px}
.promo-head .dot{width:12px;height:12px;border-radius:50%;background:var(--ink)}
.promo-head .name{font-family:"Montserrat",sans-serif;font-weight:800;font-size:13px;line-height:1;color:var(--ink)}
.presents{position:absolute;left:150px;top:62px;font-family:"Great Vibes",cursive;font-size:24px;color:var(--white)}
.conf{position:absolute;left:0;width:260px;text-align:center;font-family:"Montserrat",sans-serif;font-weight:900;color:var(--yellow);
  -webkit-text-stroke:5px var(--ink);paint-order:stroke fill;line-height:1}
.conf.year{top:340px;font-size:50px}
.conf.l1{top:393px;font-size:29px}
.conf.l2{top:427px;font-size:29px}
.conf.l3{top:461px;font-size:29px}
.tagged{position:absolute;left:0;top:522px;width:260px;text-align:center;font-family:"Montserrat",sans-serif;font-weight:400;font-size:20px;letter-spacing:5px;color:var(--white)}
.big{position:absolute;left:0;width:260px;text-align:center;font-family:"Montserrat",sans-serif;font-weight:900;line-height:1;color:var(--red);
  -webkit-text-stroke:4px var(--white);paint-order:stroke fill;letter-spacing:-3px}
.big.love{top:549px;font-size:68px}
.big.lust{top:661px;font-size:68px}
.or{position:absolute;left:0;top:623px;width:260px;text-align:center;font-family:"Montserrat",sans-serif;font-weight:900;font-size:32px;line-height:1;color:var(--white)}
.pitch{position:absolute;left:0;width:260px;text-align:center;font-family:"Montserrat",sans-serif;font-weight:400;color:var(--white);line-height:1}
.pitch.a{top:747px;font-size:15px}
.pitch.b{top:768px;font-size:26px}
.pitch.c{top:797px;font-size:26px}
.pitch.d{top:828px;font-size:15px}
.rule{position:absolute;left:54px;width:152px;height:1px;background:linear-gradient(90deg,transparent,#fff,transparent)}
.rule.top{top:864px}
.rule.bot{top:921px}
.minister{position:absolute;left:0;width:260px;text-align:center;font-family:"Montserrat",sans-serif;line-height:1}
.minister.label{top:868px;font-size:15px;color:var(--yellow);font-weight:500}
.minister.name{top:885px;font-size:20px;color:var(--white);font-weight:800}
.minister.role{top:906px;font-size:12px;color:var(--white);font-weight:400}
.cal{position:absolute;left:36px;top:940px}
.date{position:absolute;left:105px;font-family:"Montserrat",sans-serif;color:var(--white);line-height:1}
.date.day{top:935px;font-size:13px}
.date.day span{color:var(--yellow)}
.date.num{top:951px;font-size:40px;font-weight:900}
.date.time{top:987px;font-size:14px}
.date.time span{color:var(--yellow);margin-right:8px}
.promo-foot{position:absolute;left:0;bottom:0;width:260px;height:4px;background:var(--yellow)}

/* Directory */
.directory{position:absolute;left:294px;top:155px;display:grid;grid-template-columns:264px 264px;grid-template-rows:repeat(5,194px);column-gap:9px;row-gap:12px}
.church{position:relative;border:2px solid var(--ink);background:var(--white);overflow:hidden}
.church-name{position:absolute;left:4px;right:4px;top:5px;height:36px;display:flex;align-items:center;justify-content:center;text-align:center;
  font-family:"Barlow Condensed",sans-serif;font-weight:700;font-size:20.5px;line-height:.88;text-transform:uppercase;white-space:nowrap}
.pastor-photo{position:absolute;left:14px;top:48px;width:100px;height:100px;background:var(--photo-yellow);border:1.5px solid var(--ink)}
.pastor{position:absolute;left:2px;width:124px;top:155px;text-align:center;font-family:"Barlow Semi Condensed",sans-serif;font-weight:600;font-size:13px;line-height:.95;text-transform:uppercase}
.info{position:absolute;left:120px;right:2px;top:51px;text-align:center}
.service{font-family:"Barlow Semi Condensed",sans-serif;font-weight:600;font-size:16px;line-height:1.05}
.extra{font-size:9.5px;line-height:1.05;margin-top:1px}
.address{font-size:9.5px;line-height:1.3;margin-top:10px}
.fine{font-family:"Barlow Condensed",sans-serif;font-weight:600;font-size:7px;line-height:1.35;text-transform:uppercase;margin-top:4px}
.fine-sm{font-family:"Barlow Condensed",sans-serif;font-weight:600;font-size:7.8px;line-height:1.3}
.phone{position:absolute;left:120px;top:157px;display:flex;align-items:center}
.phone .ico{width:23px;height:23px;border-radius:50%;background:var(--ink);display:flex;align-items:center;justify-content:center;position:relative;z-index:1}
.phone .num{background:var(--band);margin-left:-3px;padding:0 4px 0 10px;width:120px;height:14px;display:flex;align-items:center;
  font-family:"Barlow Semi Condensed",sans-serif;font-weight:600;font-size:16px;color:#1a1a1a}
.phone .num.duo{height:auto;flex-direction:column;align-items:flex-start;line-height:1.15;padding-top:1px;background:linear-gradient(var(--band) 50%,transparent 50%)}
</style>
</head>
<body>

<header class="banner">
  <div class="banner-scene" role="img" aria-label="White country church beside a sunset sky over a grassy field"></div>
  <svg class="banner-cross" width="40" height="44" viewBox="0 0 40 44"><rect x="18" y="0" width="4" height="44" fill="#c76a3a"/><rect x="4" y="10" width="32" height="4" fill="#c76a3a"/></svg>
  <h1 class="banner-title">CHURCH DIRECTORY</h1>
</header>

<aside class="promo">
  <div class="promo-photo" role="img" aria-label="Laughing couple embracing, woman riding on man's back"></div>
  <div class="promo-head"><span class="dot"></span><span class="name">WE LET MINISTRIES</span></div>
  <div class="presents">Presents</div>
  <div class="conf year">2023</div>
  <div class="conf l1">COUPLES &amp;</div>
  <div class="conf l2">SINGLES</div>
  <div class="conf l3">CONFERENCE</div>
  <div class="tagged">TAGGED:</div>
  <div class="big love">LOVE</div>
  <div class="or">OR</div>
  <div class="big lust">LUST</div>
  <div class="pitch a">COME AND GET YOUR</div>
  <div class="pitch b">MARRIAGE,</div>
  <div class="pitch c">RELATIONSHIP</div>
  <div class="pitch d">BACK AGAIN</div>
  <div class="rule top"></div>
  <div class="minister label">MINISTERING:</div>
  <div class="minister name">DR. RO DUN</div>
  <div class="minister role">RELATIONSHIP EXPERT</div>
  <div class="rule bot"></div>
  <svg class="cal" width="60" height="56" viewBox="0 0 60 56" fill="none" stroke="#fff200" stroke-width="2.5">
    <rect x="12" y="5" width="44" height="40" rx="4"/><line x1="12" y1="14" x2="56" y2="14"/>
    <line x1="22" y1="1" x2="22" y2="9"/><line x1="34" y1="1" x2="34" y2="9"/><line x1="46" y1="1" x2="46" y2="9"/>
    <rect x="36" y="20" width="6" height="6"/><rect x="46" y="20" width="6" height="6"/><rect x="36" y="30" width="6" height="6"/><rect x="46" y="30" width="6" height="6"/>
    <circle cx="18" cy="38" r="15" fill="#3a0404"/><polyline points="18,29 18,38 25,41"/>
  </svg>
  <div class="date day">SUNDAY <span>SEPT.</span></div>
  <div class="date num">14TH</div>
  <div class="date time"><span>5:00PM</span>2023</div>
  <div class="promo-foot"></div>
</aside>

<main class="directory">

  <article class="church">
    <h2 class="church-name">Harvest International Min.</h2>
    <div class="pastor-photo" role="img" aria-label="Portrait of Bishop Marcus Allen Reed, Jr"></div>
    <div class="info"><div class="service">Sunday Worship<br>Service 10:30am</div><div class="address">120 Eastview Dr,<br>Pittsburgh, PA.</div></div>
    <div class="pastor">Bishop Marcus<br>Allen Reed, Jr</div>
    <div class="phone"><span class="ico"><svg width="12" height="12" viewBox="0 0 24 24"><path fill="#fff" d="M6.6 10.8a15.1 15.1 0 0 0 6.6 6.6l2.2-2.2c.3-.3.7-.4 1-.2 1.1.4 2.3.6 3.6.6.6 0 1 .4 1 1V20c0 .6-.4 1-1 1A17 17 0 0 1 3 4c0-.6.4-1 1-1h3.5c.6 0 1 .4 1 1 0 1.3.2 2.5.6 3.6.1.3 0 .7-.2 1z"/></svg></span><span class="num">(412) 555 0142</span></div>
  </article>

  <article class="church">
    <h2 class="church-name">Grace Hill Baptist Church</h2>
    <div class="pastor-photo" role="img" aria-label="Portrait of Dr. Samuel T. Brooks"></div>
    <div class="info"><div class="service">Sunday Worship<br>Service 10:30am</div><div class="address">4410 Maple Street<br>Pittsburgh, PA 15208</div></div>
    <div class="pastor">Dr. Samuel<br>T. Brooks</div>
    <div class="phone"><span class="ico"><svg width="12" height="12" viewBox="0 0 24 24"><path fill="#fff" d="M6.6 10.8a15.1 15.1 0 0 0 6.6 6.6l2.2-2.2c.3-.3.7-.4 1-.2 1.1.4 2.3.6 3.6.6.6 0 1 .4 1 1V20c0 .6-.4 1-1 1A17 17 0 0 1 3 4c0-.6.4-1 1-1h3.5c.6 0 1 .4 1 1 0 1.3.2 2.5.6 3.6.1.3 0 .7-.2 1z"/></svg></span><span class="num">(412) 555 0187</span></div>
  </article>

  <article class="church">
    <h2 class="church-name">St. Mark Baptist Church</h2>
    <div class="pastor-photo" role="img" aria-label="Pastor Linda Carver preaching at a pulpit"></div>
    <div class="info" style="top:52px"><div class="service" style="font-size:14.5px">Sunday Worship<br>Service 10:30am<br>Sunday School 8:30am</div><div class="address" style="margin-top:8px">2250 OAK AVE.<br>PITTSBURGH, PA</div></div>
    <div class="pastor">Pastor, Rev.<br>Linda Carver</div>
    <div class="phone"><span class="ico"><svg width="12" height="12" viewBox="0 0 24 24"><path fill="#fff" d="M6.6 10.8a15.1 15.1 0 0 0 6.6 6.6l2.2-2.2c.3-.3.7-.4 1-.2 1.1.4 2.3.6 3.6.6.6 0 1 .4 1 1V20c0 .6-.4 1-1 1A17 17 0 0 1 3 4c0-.6.4-1 1-1h3.5c.6 0 1 .4 1 1 0 1.3.2 2.5.6 3.6.1.3 0 .7-.2 1z"/></svg></span><span class="num">(412) 555 0163</span></div>
  </article>

  <article class="church">
    <h2 class="church-name">New Path Christian<br>Fellowship</h2>
    <div class="pastor-photo" role="img" aria-label="Apostle Gregory and Pastor Nina Hale standing together"></div>
    <div class="info" style="top:54px"><div class="service" style="font-size:14.5px">Sunday Worship<br>Service 11:00am</div><div class="extra">Wed. Bible Study @ 7:30pm<br>Saturday Prayer at 9:00am</div><div class="address" style="margin-top:12px">3150 Briarwood Street,<br>Pittsburgh, PA.</div></div>
    <div class="pastor" style="font-family:'Barlow Condensed',sans-serif;font-weight:700;font-size:11px;line-height:1.15">Apostle Gregory<br>&amp; Pastor Nina Hale</div>
    <div class="phone"><span class="ico"><svg width="12" height="12" viewBox="0 0 24 24"><path fill="#fff" d="M6.6 10.8a15.1 15.1 0 0 0 6.6 6.6l2.2-2.2c.3-.3.7-.4 1-.2 1.1.4 2.3.6 3.6.6.6 0 1 .4 1 1V20c0 .6-.4 1-1 1A17 17 0 0 1 3 4c0-.6.4-1 1-1h3.5c.6 0 1 .4 1 1 0 1.3.2 2.5.6 3.6.1.3 0 .7-.2 1z"/></svg></span><span class="num">(412) 555 0121</span></div>
  </article>

  <article class="church">
    <h2 class="church-name">Zion Community<br>Missionary Baptist Church</h2>
    <div class="pastor-photo" role="img" aria-label="Portrait of Reverend Harold D. Whitfield in a dark suit"></div>
    <div class="info" style="top:64px"><div class="fine">In-person Sunday worship<br>service 9:00am &amp; replay 6:00pm EST<br>Wednesday midweek only<br>Bible study: 2:00am - 1:00pm<br>Midweek corporate prayer: 6:00pm-7:00pm</div><div class="address" style="margin-top:6px">5520 MILLBROOK AVENUE<br>PITTSBURGH, PA 15208</div></div>
    <div class="pastor" style="font-family:'Barlow Condensed',sans-serif;font-weight:700;font-size:11.5px;line-height:1.05">Reverend Harold<br>D. Whitfield</div>
    <div class="phone"><span class="ico"><svg width="12" height="12" viewBox="0 0 24 24"><path fill="#fff" d="M6.6 10.8a15.1 15.1 0 0 0 6.6 6.6l2.2-2.2c.3-.3.7-.4 1-.2 1.1.4 2.3.6 3.6.6.6 0 1 .4 1 1V20c0 .6-.4 1-1 1A17 17 0 0 1 3 4c0-.6.4-1 1-1h3.5c.6 0 1 .4 1 1 0 1.3.2 2.5.6 3.6.1.3 0 .7-.2 1z"/></svg></span><span class="num duo" style="font-family:'Barlow Condensed',sans-serif;font-weight:700;font-size:10px"><span>412.555.0110 - CHURCH</span><span>412-555-0111 - FAX</span></span></div>
  </article>

  <article class="church">
    <h2 class="church-name">Word Center Church</h2>
    <div class="pastor-photo" role="img" aria-label="Portrait of Rev. Dr. James R. Porter Jr."></div>
    <div class="info"><div class="service">Sunday Worship<br>Service 10:0am</div><div class="address">918 N. Linden Ave.<br>Pittsburgh, PA 15208</div></div>
    <div class="pastor">Rev. Dr. James<br>R. Porter Jr.</div>
    <div class="phone"><span class="ico"><svg width="12" height="12" viewBox="0 0 24 24"><path fill="#fff" d="M6.6 10.8a15.1 15.1 0 0 0 6.6 6.6l2.2-2.2c.3-.3.7-.4 1-.2 1.1.4 2.3.6 3.6.6.6 0 1 .4 1 1V20c0 .6-.4 1-1 1A17 17 0 0 1 3 4c0-.6.4-1 1-1h3.5c.6 0 1 .4 1 1 0 1.3.2 2.5.6 3.6.1.3 0 .7-.2 1z"/></svg></span><span class="num">(412) 555 0198</span></div>
  </article>

  <article class="church">
    <h2 class="church-name">Redemption Baptist Church</h2>
    <div class="pastor-photo" role="img" aria-label="Dr. Anthony W. Grant Sr. preaching at a wooden pulpit"></div>
    <div class="info" style="top:54px"><div class="service" style="font-size:14.5px">Sunday Worship<br>Service 11:00am</div><div class="address" style="margin-top:20px">640 Riverside Ave,<br>PITTSBURGH, PA</div></div>
    <div class="pastor">Dr. Anthony<br>W. Grant Sr.</div>
    <div class="phone"><span class="ico"><svg width="12" height="12" viewBox="0 0 24 24"><path fill="#fff" d="M6.6 10.8a15.1 15.1 0 0 0 6.6 6.6l2.2-2.2c.3-.3.7-.4 1-.2 1.1.4 2.3.6 3.6.6.6 0 1 .4 1 1V20c0 .6-.4 1-1 1A17 17 0 0 1 3 4c0-.6.4-1 1-1h3.5c.6 0 1 .4 1 1 0 1.3.2 2.5.6 3.6.1.3 0 .7-.2 1z"/></svg></span><span class="num">(412) 555 0176</span></div>
  </article>

  <article class="church">
    <h2 class="church-name">Faith Temple Church<br>Pittsburgh (FTC-PGH)</h2>
    <div class="pastor-photo" role="img" aria-label="Rev. Calvin Adam Moore standing with his wife"></div>
    <div class="info" style="top:52px"><div class="service">Sunday Worship<br>Service 8:00am<br>&amp; 10:45am</div><div class="address" style="margin-top:6px">3380 ELM STREET,<br>PITTSBURGH, PA. 15208</div></div>
    <div class="pastor">Rev. Calvin<br>Adam Moore</div>
    <div class="phone"><span class="ico"><svg width="12" height="12" viewBox="0 0 24 24"><path fill="#fff" d="M6.6 10.8a15.1 15.1 0 0 0 6.6 6.6l2.2-2.2c.3-.3.7-.4 1-.2 1.1.4 2.3.6 3.6.6.6 0 1 .4 1 1V20c0 .6-.4 1-1 1A17 17 0 0 1 3 4c0-.6.4-1 1-1h3.5c.6 0 1 .4 1 1 0 1.3.2 2.5.6 3.6.1.3 0 .7-.2 1z"/></svg></span><span class="num">(412) 555 0134</span></div>
  </article>

  <article class="church">
    <h2 class="church-name">Still Waters Church</h2>
    <div class="pastor-photo" role="img" aria-label="Black and white portrait of Pst. Henry T. Wells"></div>
    <div class="info"><div class="service">Sunday Worship<br>Service 10:30am</div><div class="address">2015 Cedar Street<br>Pittsburgh, PA 15208</div></div>
    <div class="pastor">Pst. Henry<br>T. Wells</div>
    <div class="phone"><span class="ico"><svg width="12" height="12" viewBox="0 0 24 24"><path fill="#fff" d="M6.6 10.8a15.1 15.1 0 0 0 6.6 6.6l2.2-2.2c.3-.3.7-.4 1-.2 1.1.4 2.3.6 3.6.6.6 0 1 .4 1 1V20c0 .6-.4 1-1 1A17 17 0 0 1 3 4c0-.6.4-1 1-1h3.5c.6 0 1 .4 1 1 0 1.3.2 2.5.6 3.6.1.3 0 .7-.2 1z"/></svg></span><span class="num">(412) 555 0157</span></div>
  </article>

  <article class="church">
    <h2 class="church-name">Hillside Street Missionary<br>Baptist Church</h2>
    <div class="pastor-photo" role="img" aria-label="Portrait of Rev. Dr. Kevin T. Dawson"></div>
    <div class="info" style="top:55px"><div class="fine-sm">Church Service Join us Virtually<br>Sunday Academy 7:30am<br>Sunday Worship 9am, 2pm, 7pm, 10pm<br>Mondays 8am and 12 Noon<br>Wednesday at 12Noon<br>Saturdays at 10pm</div><div class="address" style="margin-top:7px">4020 Hillside St.<br>Pittsburgh, PA</div></div>
    <div class="pastor">Rev. Dr. Kevin<br>T. Dawson</div>
    <div class="phone"><span class="ico"><svg width="12" height="12" viewBox="0 0 24 24"><path fill="#fff" d="M6.6 10.8a15.1 15.1 0 0 0 6.6 6.6l2.2-2.2c.3-.3.7-.4 1-.2 1.1.4 2.3.6 3.6.6.6 0 1 .4 1 1V20c0 .6-.4 1-1 1A17 17 0 0 1 3 4c0-.6.4-1 1-1h3.5c.6 0 1 .4 1 1 0 1.3.2 2.5.6 3.6.1.3 0 .7-.2 1z"/></svg></span><span class="num">(412) 555 0119</span></div>
  </article>

</main>
</body>
</html>
```